Business Card Design

WE are looking for a premium quality Business Cards for a Law Firm . Copies of our current business card is attached.

Contact Information for Business Card

xyz

```html
<!DOCTYPE html>
<html lang="en">
<head>
<meta charset="utf-8">
<title>Harcourt Lawyers – Business Cards</title>
<link href="https://fonts.googleapis.com/css2?family=Cinzel:wght@600;700&family=Arimo:wght@400;700&display=swap" rel="stylesheet">
<style>
  :root {
    --bg: #2a2a2c;
    --card: #fbfbfa;
    --green: #14352a;
    --gold: #b8944f;
    --ink: #2b2b2b;
  }
  * { margin: 0; padding: 0; box-sizing: border-box; }
  html, body { width: 1200px; height: 779px; overflow: hidden; }
  body {
    background: var(--bg);
    font-family: "Arimo", Arial, sans-serif;
    color: var(--ink);
    position: relative;
  }
  .card {
    position: absolute;
    width: 560px;
    height: 320px;
    background: var(--card);
    border-bottom: 3px solid var(--gold);
  }
  .card--offices { left: 50px; top: 60px; }
  .card--person { left: 590px; top: 395px; }

  .brand {
    position: absolute;
    left: 0; right: 0;
    text-align: center;
  }
  .brand__circle {
    width: 46px; height: 46px;
    border: 3px solid var(--gold);
    border-radius: 50%;
    margin: 0 auto 10px;
  }
  .brand__name {
    font-family: "Cinzel", Georgia, serif;
    font-weight: 700;
    font-size: 28px;
    letter-spacing: 1px;
    color: var(--green);
    line-height: 1;
  }

  .card--offices .brand { top: 44px; }
  .offices {
    position: absolute;
    left: 0; right: 0; bottom: 44px;
    display: flex;
    justify-content: center;
    align-items: flex-end;
  }
  .office {
    width: 170px;
    text-align: center;
    font-size: 11px;
    line-height: 1.4;
    padding: 4px 8px;
  }
  .office + .office { border-left: 1.5px solid var(--gold); }
  .office__city { font-weight: 700; font-size: 12px; color: var(--green); }
  .office__label { font-weight: 700; }
  .office--mid { margin-bottom: 22px; }
  .office--top { margin-bottom: 44px; }

  .card--person .brand { left: 200px; right: 0; top: 28px; }
  .person {
    position: absolute;
    left: 40px; top: 200px;
    width: 230px;
    text-align: right;
  }
  .person__name {
    font-family: "Cinzel", Georgia, serif;
    font-weight: 700;
    font-size: 24px;
    color: var(--green);
    letter-spacing: 1px;
  }
  .person__role {
    font-size: 14px;
    color: var(--gold);
    line-height: 1.35;
    margin-top: 4px;
  }
  .divider {
    position: absolute;
    left: 292px; top: 150px;
    width: 1.5px; height: 140px;
    background: #b9b9b9;
  }
  .contact {
    position: absolute;
    left: 312px; top: 150px;
    font-size: 13.5px;
    line-height: 1.35;
  }
  .contact__address { margin-bottom: 6px; }
  .contact__row { display: flex; align-items: center; gap: 8px; }
  .contact__row svg { width: 12px; height: 12px; fill: var(--green); flex: none; }
</style>
</head>
<body>

<section class="card card--offices">
  <div class="brand">
    <div class="brand__circle"></div>
    <div class="brand__name">Harcourt Lawyers</div>
  </div>
  <div class="offices">
    <div class="office">
      <div class="office__city">Melbourne</div>
      Level 27, 210 Elm Street<br>Melbourne, VIC 3001<br>
      <span class="office__label">Phone :</span> +61 03 9000 1122
    </div>
    <div class="office office--mid">
      <div class="office__city">Sydney</div>
      Level 15, Crestline Building<br>42 Market Lane<br>Parramatta, NSW 2151<br>
      <span class="office__label">Phone :</span> +61 02 9000 3344
    </div>
    <div class="office office--top">
      <div class="office__city">Perth</div>
      Level 28, Meridian Tower<br>75 Harbour Terrace<br>Perth, WA 6001<br>
      <span class="office__label">Phone :</span> +61 08 9000 5566
    </div>
  </div>
</section>

<section class="card card--person">
  <div class="brand">
    <div class="brand__circle"></div>
    <div class="brand__name">Harcourt Lawyers</div>
  </div>
  <div class="person">
    <div class="person__name">Daniel Reyes</div>
    <div class="person__role">Director &amp; Principal Solicitor<br>MBA, Juris Doctor</div>
  </div>
  <div class="divider"></div>
  <div class="contact">
    <div class="contact__address">Level 3, Harcourt House<br>88 Ridgeview Terrace<br>Brookfield, QLD 4001</div>
    <div class="contact__row">
      <svg viewBox="0 0 24 24"><path d="M6.6 10.8a15 15 0 0 0 6.6 6.6l2.2-2.2a1 1 0 0 1 1-.25 11.4 11.4 0 0 0 3.6.57 1 1 0 0 1 1 1V20a1 1 0 0 1-1 1A17 17 0 0 1 3 4a1 1 0 0 1 1-1h3.5a1 1 0 0 1 1 1c0 1.25.2 2.45.57 3.57a1 1 0 0 1-.25 1z"/></svg>
      +61 7 3000 1234
    </div>
    <div class="contact__row">
      <svg viewBox="0 0 24 24"><path d="M7 1h10a2 2 0 0 1 2 2v18a2 2 0 0 1-2 2H7a2 2 0 0 1-2-2V3a2 2 0 0 1 2-2zm0 3v14h10V4zm5 15.5a1.2 1.2 0 1 0 0 2.4 1.2 1.2 0 0 0 0-2.4z"/></svg>
      +61 0400 555 018
    </div>
    <div class="contact__row">
      <svg viewBox="0 0 24 24"><path d="M2 5h20v14H2zm2 2v.5l8 5 8-5V7zm0 2.8V17h16V9.8l-8 5z"/></svg>
      daniel@harcourtlawyers.com.au
    </div>
    <div class="contact__row">
      <svg viewBox="0 0 24 24"><circle cx="12" cy="12" r="10"/></svg>
      www.harcourtlawyers.com.au
    </div>
  </div>
</section>

</body>
</html>
```